Financial Planning business needs a Web Design

Web design needed for financial planning business that encompasses investments, insurance and corporate planning. Would like a sleek, simple design that includes elements of nature/trees and lifestyle based imagery, with an overall feel of trustworthiness, security, growth and freedom. We like the layout of www.quellmarkroanefinancial.example, torvinfinancial.example and plomtavery.example, but with more color and images consistent with the nature/lifestyle theme.

Target Market(s)

New and existing clients

Industry/Entity Type

Financial

Number of Pages Required

5+ page

Requirements
Nice to have
• link to twitter feed
• 'latest features' link to articles
• links to action - buy insurance, get a quote, etc/

```html
<!DOCTYPE html>
<html lang="en">
<head>
<meta charset="utf-8">
<title>Wrenfield Wealth Planning</title>
<link href="https://fonts.googleapis.com/css2?family=Arimo:wght@400;700&family=Open+Sans:wght@400;600;700&display=swap" rel="stylesheet">
<style>
:root{
  --leaf:#6db32c;
  --leaf-btn:#5aa51f;
  --olive:#7f9a2a;
  --forest:#1f6e1f;
  --ink:#333;
  --muted:#777;
  --rule:#e3e3e3;
  --panel:#f5f5f5;
  --chip:#dcdcdc;
}
*{margin:0;padding:0;box-sizing:border-box}
html,body{width:738px;height:1200px;overflow:hidden}
body{position:relative;font-family:"Arimo",Arial,sans-serif;color:var(--ink)}
.backdrop{position:absolute;inset:0;background:radial-gradient(ellipse at 50% 40%,#c9ec8a 0%,#7fc934 45%,#4f9e1a 100%)}
.page{position:absolute;left:90px;top:22px;width:559px;height:1154px;background:#fff}
.abs{position:absolute}
.brand-mark{left:20px;top:14px;width:34px;height:34px;background:var(--leaf)}
.brand-name{left:68px;top:18px;font:400 17px "Open Sans",sans-serif;color:var(--forest)}
.brand-sub{left:69px;top:42px;font:400 7.5px "Arimo",sans-serif;letter-spacing:2px;color:var(--muted)}
.btn{display:flex;align-items:center;justify-content:center;color:#fff;font:700 8px "Arimo",sans-serif;text-transform:uppercase}
.btn-insure{left:312px;top:22px;width:97px;height:28px;background:var(--leaf-btn);box-shadow:0 1px 2px rgba(0,0,0,.25)}
.social{display:flex;gap:6px}
.social span{width:16px;height:16px;border-radius:50%;background:var(--chip)}
.social-top{left:426px;top:29px}
.nav{left:0;top:68px;width:559px;height:28px;border-top:1px solid var(--rule);border-bottom:1px solid var(--rule);display:flex;justify-content:space-between;align-items:center;padding:0 26px 0 31px;font:700 8px "Arimo",sans-serif;color:#555}
.nav .active{color:var(--leaf)}
.hero{left:0;top:97px;width:559px;height:288px;background:linear-gradient(100deg,#d8d9dc 0%,#b9bcc2 35%,#f0f0f0 55%,#2d3440 85%,#1f2530 100%)}
.hero-title{left:20px;top:196px;font:700 13.5px/21px "Arimo",sans-serif;color:#fff;text-shadow:0 1px 2px rgba(0,0,0,.4)}
.btn-quote{left:21px;top:305px;width:104px;height:30px;background:var(--olive)}
h2{font:700 14px "Arimo",sans-serif;color:var(--leaf)}
p{font-size:7.2px;line-height:14px;color:var(--ink)}
.photo{border:2px solid #fff;box-shadow:0 0 0 1px #ddd}
.wwd-photo{left:21px;top:448px;width:213px;height:98px;background:linear-gradient(90deg,#9fc4dc,#d7e8f2 50%,#6f95b3)}
.about-lead{font:700 10.3px/15px "Arimo",sans-serif;color:var(--forest)}
.features{left:0;top:632px;width:559px;height:272px;background:var(--panel);border-top:1px solid var(--rule);border-bottom:1px solid var(--rule)}
.card{position:absolute;top:68px;width:161px}
.card .photo{height:114px;background:linear-gradient(120deg,#e8eaee,#b8bec8 50%,#3b4250)}
.card h3{margin-top:16px;font:600 9.5px "Open Sans",sans-serif;color:var(--forest)}
.card p{margin-top:1px}
.tweet .handle{font-style:italic;color:var(--forest)}
.tweet .time{color:var(--olive);font-family:"Open Sans",sans-serif}
.divider{height:1px;background:var(--rule)}
.testimonial{left:278px;top:961px;width:260px;height:123px;background:#f2f2f2}
.avatar{left:10px;top:19px;width:40px;height:40px;border-radius:50%;background:linear-gradient(#cfd8e0,#8fa0b0);border:2px solid #fff;box-shadow:0 0 0 1px #ddd}
.quote-mark{left:76px;top:8px;font:700 16px "Arimo",sans-serif;color:#bbb}
.client{color:var(--olive);font-family:"Open Sans",sans-serif}
.dots{left:226px;top:101px;display:flex;gap:2px}
.dots span{width:11px;height:3px;background:#ccc}
.dots .on{background:var(--forest)}
.foot-rule{left:20px;top:1106px;width:531px}
.copy{left:21px;top:1126px;font-size:6.5px}
.social-foot{left:421px;top:1121px;gap:5px}
.social-foot span{width:19px;height:19px;background:#cfcfcf}
</style>
</head>
<body>
<div class="backdrop" role="img" aria-label="Soft green leafy backdrop with glowing light"></div>
<div class="page">
  <div class="abs brand-mark"></div>
  <div class="abs brand-name">Wrenfield</div>
  <div class="abs brand-sub">WEALTH PLANNING</div>
  <a class="abs btn btn-insure">Buy Insurance</a>
  <div class="abs social social-top"><span></span><span></span><span></span><span></span><span></span></div>
  <nav class="abs nav"><span class="active">Home</span><span>What We Do</span><span>Articles</span><span>Team</span><span>Newsletter</span><span>Contact</span><span>Login</span></nav>

  <div class="abs hero" role="img" aria-label="Business team meeting around a table"></div>
  <div class="abs hero-title">Torvin Financial has the professional<br>expertise you're looking for...</div>
  <a class="abs btn btn-quote">Get a Quote</a>

  <h2 class="abs" style="left:22px;top:412px">What We Do</h2>
  <div class="abs photo wwd-photo" role="img" aria-label="Advisor in a suit in a bright office"></div>
  <p class="abs" style="left:23px;top:562px;width:210px">Lorem quis bibendum auctor, nisi elit consequat ipsum, nec sagittis sem nibh id elit. Duis sed odio sit amet nibh vulputate cursus a sit amet mauris.</p>

  <h2 class="abs" style="left:278px;top:411px">About us</h2>
  <div class="abs about-lead" style="left:277px;top:444px;width:265px">Aenean sollicitudin, lorem quis bibendum auctor, nisi elit consequat ipsum, nec sagittis sem.</div>
  <p class="abs" style="left:279px;top:485px;width:248px">Lorem quis bibendum auctor, nisi elit consequat ipsum, nec sagittis sem nibh id elit.quis bibendum auctor, nisi elit consequat ipsum, nec sagittis sem nibh id elit This is Photoshop's version of Lorem Ipsum. Proin gravida nibh vel velit auctor aliquet. Aenean sollicitudin.</p>
  <p class="abs" style="left:278px;top:548px;width:250px">Duis sed odio sit amet nibh vulputate cursus a sit amet mauris. Morbi accumsan ipsum velit. Nam nec tellus a odio tincidunt auctor a ornare odio. <span style="color:var(--leaf)">Read More</span></p>

  <section class="abs features">
    <h2 class="abs" style="left:0;width:559px;top:30px;text-align:center">Latest Features / Articles</h2>
    <div class="card" style="left:20px"><div class="photo" role="img" aria-label="Colleagues discussing charts at a desk"></div><h3>Financial Planning</h3><p>This is Photoshop's version of Lorem Ipsum gravida nibh vel velit auctor aliquet....</p></div>
    <div class="card" style="left:200px"><div class="photo" role="img" aria-label="Team meeting with a tablet"></div><h3>Financial Planning</h3><p>This is Photoshop's version of Lorem Ipsum gravida nibh vel velit auctor aliquet....</p></div>
    <div class="card" style="left:378px"><div class="photo" role="img" aria-label="Group reviewing documents at a table"></div><h3>Financial Planning</h3><p>This is Photoshop's version of Lorem Ipsum gravida nibh vel velit auctor aliquet....</p></div>
  </section>

  <h2 class="abs" style="left:22px;top:933px">Latest Tweets</h2>
  <div class="abs tweet" style="left:22px;top:960px;width:230px"><p><span class="handle">@Lorem ipsumdolor</span> Duis sed odio sit amet nibh vulputate cursus a sit amet mauris. Morbi accumsan ipsum velit. Nam nec tellus a odio.<br><span class="time">10 minutes ago</span></p></div>
  <div class="abs divider" style="left:22px;top:1014px;width:224px"></div>
  <div class="abs tweet" style="left:22px;top:1026px;width:230px"><p><span class="handle">@Lorem ipsumdolor</span> Duis sed odio sit amet nibh vulputate cursus a sit amet mauris. Morbi accumsan ipsum velit. Nam nec tellus a odio.<br><span class="time">10 minutes ago</span></p></div>

  <h2 class="abs" style="left:279px;top:924px">Testimonial</h2>
  <div class="abs testimonial">
    <div class="abs avatar" role="img" aria-label="Client portrait"></div>
    <div class="abs quote-mark">&#8221;</div>
    <p class="abs" style="left:72px;top:30px;width:170px">Duis sed odio sit amet nibh vulputate cursus a sit amet mauris. Morbi accumsan ipsum velit. Nam nec tellus a odio<br><span class="client" style="line-height:22px">Client Name Here</span></p>
    <div class="abs dots"><span></span><span class="on"></span></div>
  </div>

  <div class="abs divider foot-rule"></div>
  <p class="abs copy">© 2015. Site Name. All Rights Reserved.</p>
  <div class="abs social social-foot"><span></span><span></span><span></span><span></span><span></span></div>
</div>
</body>
</html>
```